Clear Path Keystone Realty yard sign Logo

UPDATE Design logo for Realty yard sign. 24x24 diamond or 36x24 Rectangle.
Open to all ideas. We are a discount firm but want to project a high end feel. We provide 100% of all services and extensive marketing for 1/2 the fee.
The following info must be on sign
CLEAR PATH KEYSTONE (OR K) REALTY
Doran Pike 547-6093
KeystonePX.com

Target Market(s)

home sellers and buyers

Industry/Entity Type

Real Estate yard sign please see sign attached in gif

Logo Text

Clear Path Keystone Realty OR (K IN PLACE OF KEYSTONE)

Requirements
Must have
• CLEAR PATH KEYSTONE (OR K) REALTY Doran Pike 547-6093 KeystonePX.com FOR SALE (optional)

```html
<!DOCTYPE html>
<html lang="en">
<head>
<meta charset="utf-8">
<title>Clear Path Keystone Realty — Yard Sign</title>
<link rel="stylesheet" href="https://fonts.googleapis.com/css2?family=Montserrat:wght@700;800&display=swap">
<style>
  :root {
    --sign-black: #0a0a0a;
    --brand-red: #ee0a1b;
    --ink-white: #ffffff;
    --backdrop: #f2f2f0;
  }
  html, body {
    margin: 0;
    padding: 0;
    width: 1200px;
    height: 1199px;
    overflow: hidden;
    background: var(--backdrop);
  }
  .yard-sign {
    display: block;
    width: 1200px;
    height: 1199px;
  }
  .sign-panel { fill: var(--sign-black); }
  .badge-disc { fill: var(--brand-red); }
  .brand-name {
    font-family: "Montserrat", sans-serif;
    font-weight: 800;
    fill: var(--ink-white);
    letter-spacing: 3px;
  }
  .agent-details {
    font-family: "Montserrat", sans-serif;
    font-weight: 700;
    fill: var(--ink-white);
  }
</style>
</head>
<body>
<svg class="yard-sign" viewBox="0 0 1200 1199" xmlns="http://www.w3.org/2000/svg" aria-label="Clear Path Keystone Realty diamond yard sign">
  <polygon class="sign-panel" points="590,217 972,599 590,981 208,599"/>

  <circle class="badge-disc" cx="590" cy="599" r="233"/>

  <g class="brand-lockup" text-anchor="middle">
    <text class="brand-name" x="590" y="500" font-size="38">CLEAR PATH</text>
    <text class="brand-name" x="590" y="548" font-size="38">KEYSTONE</text>
    <text class="brand-name" x="590" y="596" font-size="38">REALTY</text>
  </g>

  <g class="agent-contact" text-anchor="middle">
    <text class="agent-details" x="590" y="660" font-size="26">Doran Pike</text>
    <text class="agent-details" x="590" y="692" font-size="26">547-6093</text>
    <text class="agent-details" x="590" y="724" font-size="26">KeystonePX.com</text>
  </g>
</svg>
</body>
</html>
```